Marwick Family Chiropractic Stationary

The letterhead and business card must have our logo.
We would like to see the logo used in different ways ( It can be expanded upon in the stationary.)
Please use the the same or similar colors.
Must be eye catching and memorable.
Must be easy to read

Reason: The doctor has been too busy to make any final decisions. He would like to give himself a little more time.

Target Market(s)

Chiropractic Healthcare

Industry/Entity Type

Business

Requirements
Must have
• Dr. Leonard Marwick D.C.
Chiropractor

860-555-0183

417 Birchfield Road, 2nd Floor
Linden Vale, NH 06091

drmarwick@marwickspine.example
www.marwickspine.example
www.facebook.com/MarwickFamilySpine
Should not have
• should not be difficult to read

```html
<!DOCTYPE html>
<html lang="en">
<head>
<meta charset="utf-8">
<title>Marwick Family Chiropractic – Business Cards</title>
<link rel="stylesheet" href="https://fonts.googleapis.com/css2?family=Jost:wght@400;500;600;700&display=swap">
<style>
  :root {
    --backdrop: #e9e6e1;
    --card-black: #000000;
    --leaf-green: #a6ce5a;
    --bright-green: #9fcb4e;
    --taupe: #9b9188;
    --white: #ffffff;
    --pattern-dark: #1a1a12;
    --pattern-olive: #2c3418;
    --social-blue: #3b5ea8;
  }
  * { box-sizing: border-box; margin: 0; padding: 0; }
  html, body { width: 1200px; height: 720px; overflow: hidden; }
  body {
    background: var(--backdrop);
    font-family: "Jost", "Futura", sans-serif;
    position: relative;
  }
  .card {
    position: absolute;
    width: 544px;
    height: 310px;
    overflow: hidden;
    background: var(--card-black);
    box-shadow: 0 2px 6px rgba(0,0,0,.25);
  }
  .card--contact { left: 42px; top: 36px; }
  .card--mark    { left: 618px; top: 36px; }
  .card--pattern { left: 42px; top: 372px; }
  .card--green   { left: 618px; top: 368px; background: var(--leaf-green); }

  .brand { position: absolute; text-align: center; font-weight: 600; }
  .brand__dot { display: block; margin: 0 auto 12px; border-radius: 50%; }
  .brand__line { display: block; line-height: 1.05; }

  .card--contact .brand { left: 28px; top: 34px; width: 218px; color: var(--leaf-green); }
  .card--contact .brand__dot { width: 130px; height: 130px; background: var(--leaf-green); }
  .card--contact .brand__main { font-size: 38px; letter-spacing: 1px; }
  .card--contact .brand__sub { font-size: 14.5px; letter-spacing: .4px; margin-top: 3px; color: var(--taupe); }

  .divider {
    position: absolute; left: 272px; top: 34px;
    width: 2px; height: 180px; background: var(--white);
  }
  .contact { position: absolute; left: 296px; top: 52px; color: var(--white); }
  .contact__name { font-size: 17px; font-weight: 600; color: var(--leaf-green); }
  .contact__role { font-size: 14.5px; color: var(--taupe); margin-bottom: 14px; }
  .contact__list { list-style: none; font-size: 13.5px; line-height: 21.5px; }
  .contact__list li { display: flex; align-items: center; gap: 7px; }
  .contact__icon { width: 10px; height: 10px; flex: none; }
  .contact__square { width: 9px; height: 9px; background: var(--social-blue); flex: none; margin-left: 1px; }
  .contact__address { margin-top: 14px; font-size: 13.5px; line-height: 20px; }

  .card--mark .brand { left: 0; right: 0; top: 40px; color: var(--leaf-green); }
  .card--mark .brand__dot { width: 150px; height: 150px; background: var(--leaf-green); }
  .card--mark .brand__main { font-size: 24px; letter-spacing: 2px; }

  .card--green .brand { left: 0; right: 0; top: 30px; color: var(--white); }
  .card--green .brand__dot { width: 160px; height: 160px; background: var(--white); }
  .card--green .brand__main { font-size: 24px; letter-spacing: 2px; }

  .pattern-field {
    position: absolute; inset: 0;
    background: radial-gradient(circle at 50% 50%, var(--pattern-olive), var(--pattern-dark) 75%);
  }
  .card--pattern .brand { left: 0; right: 0; top: 92px; font-weight: 700; }
  .card--pattern .brand__main { font-size: 72px; letter-spacing: 3px; color: var(--bright-green); }
  .card--pattern .brand__sub { font-size: 27px; letter-spacing: 1px; margin-top: 6px; color: var(--taupe); }

  .web {
    position: absolute; left: 0; right: 0; bottom: 24px;
    text-align: center; color: var(--white);
    font-size: 15px; letter-spacing: 2.6px;
  }
</style>
</head>
<body>

<section class="card card--contact">
  <div class="brand">
    <span class="brand__dot"></span>
    <span class="brand__line brand__main">MARWICK</span>
    <span class="brand__line brand__sub">FAMILY CHIROPRACTIC</span>
  </div>
  <div class="divider"></div>
  <div class="contact">
    <p class="contact__name">Dr. Leonard Marwick D.C.</p>
    <p class="contact__role">Chiropractor</p>
    <ul class="contact__list">
      <li>
        <svg class="contact__icon" viewBox="0 0 10 10"><path d="M2 1 L4 1 L4.6 3 L3.4 4 Q4.5 6 6 6.6 L7 5.4 L9 6 L9 8 Q5 9 1.5 5 Q1 3 2 1 Z" fill="#fff"/></svg>
        860-555-0183
      </li>
      <li>
        <svg class="contact__icon" viewBox="0 0 10 10"><rect x="0.5" y="2" width="9" height="6.5" fill="#a6ce5a"/><path d="M0.5 2 L5 5.6 L9.5 2" stroke="#000" stroke-width="0.8" fill="none"/></svg>
        mymarwick@marwickspine.example
      </li>
      <li>
        <svg class="contact__icon" viewBox="0 0 10 10"><circle cx="5" cy="5" r="4.3" fill="none" stroke="#fff"/><ellipse cx="5" cy="5" rx="1.8" ry="4.3" fill="none" stroke="#fff" stroke-width="0.8"/><line x1="0.7" y1="5" x2="9.3" y2="5" stroke="#fff" stroke-width="0.8"/></svg>
        www.marwickspine.example
      </li>
      <li><span class="contact__square"></span>MarwickFamilySpine</li>
    </ul>
    <p class="contact__address">417 Birchfield Road<br>2nd Floor, Linden Vale, NH 06091</p>
  </div>
</section>

<section class="card card--mark">
  <div class="brand">
    <span class="brand__dot"></span>
    <span class="brand__line brand__main">MARWICK</span>
  </div>
  <p class="web">www.marwickspine.example</p>
</section>

<section class="card card--pattern">
  <div class="pattern-field" role="img" aria-label="Repeating pattern of small tree marks in olive and green on black"></div>
  <div class="brand">
    <span class="brand__line brand__main">MARWICK</span>
    <span class="brand__line brand__sub">FAMILY CHIROPRACTIC</span>
  </div>
  <p class="web">www.marwickspine.example</p>
</section>

<section class="card card--green">
  <div class="brand">
    <span class="brand__dot"></span>
    <span class="brand__line brand__main">MARWICK</span>
  </div>
  <p class="web">www.marwickspine.example</p>
</section>

</body>
</html>
```